holloway paving service

Needs to have phone number 0418259730 and email markholloway@brightmail.com.au.
ABN 62318470915
name mark holloway

For all your concreting solutions
Excavation
Exposed & colour concrete
House & shed slabs
Driveways
Landing & steps

Contact Information for Business Card

ph 0418259730
email markholloway@brightmail.com.au.
ABN 62318470915
name mark holloway

```html
<!DOCTYPE html>
<html lang="en">
<head>
<meta charset="utf-8">
<title>Holloway Paving Service – Business Cards</title>
<link href="https://fonts.googleapis.com/css2?family=Lato:wght@400;700&family=Montserrat:wght@500;600&display=swap" rel="stylesheet">
<style>
  :root {
    --bg: #262626;
    --card-grey: #5b5b5b;
    --card-white: #ffffff;
    --orange: #ef6a23;
    --text-light: #e9e9e9;
    --text-muted: #8a8a8a;
  }
  * { box-sizing: border-box; margin: 0; padding: 0; }
  html, body { width: 1200px; height: 900px; overflow: hidden; }
  body {
    background: var(--bg);
    font-family: "Lato", Arial, sans-serif;
    position: relative;
  }
  .card {
    position: absolute;
    width: 540px;
    height: 310px;
    border-radius: 4px;
    overflow: hidden;
    box-shadow: 0 18px 40px rgba(0,0,0,.55);
  }

  /* Back card */
  .card-back {
    left: 610px; top: 120px;
    background: var(--card-grey);
  }
  .brand {
    position: absolute;
    left: 0; right: 0; top: 72px;
    display: flex; align-items: center; justify-content: center; gap: 18px;
  }
  .brand-mark { width: 44px; height: 44px; background: var(--orange); }
  .brand-divider { width: 1px; height: 74px; background: var(--orange); }
  .wordmark {
    font-family: "Montserrat", Arial, sans-serif;
    font-weight: 600;
    color: var(--orange);
    text-transform: uppercase;
    letter-spacing: 1px;
    font-size: 19px;
    line-height: 1.2;
  }
  .wordmark-line { display: flex; align-items: center; justify-content: center; gap: 8px; }
  .wordmark-line::before, .wordmark-line::after {
    content: ""; height: 1.5px; width: 30px; background: var(--text-light);
  }
  .brand-phone {
    font-family: "Montserrat", Arial, sans-serif;
    font-weight: 500;
    color: var(--orange);
    letter-spacing: 3px;
    font-size: 16px;
    text-align: center;
    margin-top: 2px;
  }
  .website {
    position: absolute; left: 0; right: 0; top: 178px;
    text-align: center; color: var(--text-light); font-size: 15px;
  }
  .website .accent { color: var(--orange); }
  .offer {
    position: absolute; left: 30px; right: 30px; bottom: 22px;
    text-align: center;
  }
  .tagline {
    font-family: "Montserrat", Arial, sans-serif; font-weight: 500;
    color: var(--orange); font-size: 12px; letter-spacing: 1px;
    text-transform: uppercase; margin-bottom: 8px;
  }
  .services {
    list-style: none; display: flex; flex-wrap: wrap; justify-content: center;
    gap: 4px 14px; color: var(--text-light); font-size: 12px;
  }
  .services li { display: flex; align-items: center; gap: 6px; }
  .services li::before {
    content: ""; width: 5px; height: 5px; background: var(--orange);
  }

  /* Front card */
  .card-front {
    left: 50px; top: 470px;
    background: var(--card-white);
  }
  .front-lower {
    position: absolute; left: 0; right: 0; bottom: 0; height: 140px;
    background: var(--card-grey);
  }
  .person { position: absolute; left: 30px; top: 30px; }
  .person-name {
    font-size: 26px; font-weight: 700; color: var(--orange);
    text-transform: uppercase; letter-spacing: .5px;
  }
  .person-role { font-size: 12px; color: var(--text-muted); margin-top: 2px; }
  .front-brand { position: absolute; right: 36px; top: 76px; text-align: center; }
  .front-brand .wordmark { font-size: 17px; }
  .front-brand .wordmark-line::before,
  .front-brand .wordmark-line::after { background: var(--card-grey); }
  .front-brand .brand-phone { font-size: 14px; }
  .contact {
    position: absolute; left: 30px; bottom: 14px;
    color: var(--text-light); font-size: 12px; line-height: 1.5;
    list-style: none;
  }
  .contact li { display: flex; align-items: center; gap: 7px; }
  .contact .plain { padding-left: 17px; }
  .contact svg { width: 10px; height: 10px; fill: var(--text-light); }
  .corner { position: absolute; right: 0; bottom: 0; width: 230px; height: 190px; }
  .corner-name {
    position: absolute; right: 16px; bottom: 20px;
    display: flex; align-items: center; gap: 8px;
    font-family: "Montserrat", Arial, sans-serif; font-weight: 600;
    color: var(--card-white); font-size: 11px; text-transform: uppercase;
    letter-spacing: 1px;
  }
  .corner-name .square { width: 12px; height: 12px; background: var(--card-white); }
</style>
</head>
<body>

<section class="card card-back">
  <div class="brand">
    <div class="brand-mark"></div>
    <div class="brand-divider"></div>
    <div>
      <div class="wordmark">
        <div class="wordmark-line">Holloway Paving</div>
        <div class="wordmark-line">Service</div>
      </div>
      <div class="brand-phone">0418259730</div>
    </div>
  </div>
  <p class="website">www.<span class="accent">hollowaypaving</span>.com.au</p>
  <div class="offer">
    <p class="tagline">For all your concreting solutions</p>
    <ul class="services">
      <li>Excavation</li>
      <li>Exposed &amp; colour concrete</li>
      <li>House &amp; shed slabs</li>
      <li>Driveways</li>
      <li>Landing &amp; steps</li>
    </ul>
  </div>
</section>

<section class="card card-front">
  <div class="front-lower"></div>
  <div class="person">
    <h1 class="person-name">Mark Holloway</h1>
    <p class="person-role">Director</p>
  </div>
  <div class="front-brand">
    <div class="wordmark">
      <div class="wordmark-line">Holloway Paving</div>
      <div class="wordmark-line">Service</div>
    </div>
    <div class="brand-phone">0418259730</div>
  </div>
  <ul class="contact">
    <li class="plain">Northgate, Ashby Vale, Tasmania 7099</li>
    <li><svg viewBox="0 0 10 10"><path d="M2 0h2l1 3-1.3 1a6 6 0 0 0 2.3 2.3L7 5l3 1v2a2 2 0 0 1-2 2A8 8 0 0 1 0 2a2 2 0 0 1 2-2z"/></svg>+61 418 259 730</li>
    <li><svg viewBox="0 0 10 10"><path d="M0 2h10v6H0z M0 2l5 3 5-3" fill="none" stroke="#e9e9e9" stroke-width="1"/></svg>markholloway@brightmail.com.au</li>
    <li><svg viewBox="0 0 10 10"><circle cx="5" cy="5" r="4" fill="none" stroke="#e9e9e9" stroke-width="1.4"/></svg>www.hollowaypaving.com.au</li>
    <li class="plain">ABN 62318470915</li>
  </ul>
  <svg class="corner" viewBox="0 0 230 190" aria-hidden="true">
    <polygon points="230,0 230,190 40,190" fill="#ef6a23"/>
  </svg>
  <div class="corner-name"><span class="square"></span>Holloway Paving Service</div>
</section>

</body>
</html>
```